K & R Acre Works. Business card design

We need a business card designed for a new business. We have a bulldozer and tractor service. We clear land and make wildlife food plots. We provide disking, bush hogging, and site prep services.
I have attached an image of a business card that I like and would like my business cards to look similar.

Target Market(s)

anyone needing bulldozer and/or tractor services

Industry/Entity Type

Business

Contact Information for Business Card

K & R Acre Works, Operated by 7-T-Ranch
Wade Colton
601-472-3358
wcr4817@fieldmail-example.com

Font styles to use
Sans Serif

Colors

Designer to choose colors to be used in the design.

Requirements
Must have
• image of tractor and bulldozer
• Land Clearing
• Wildlife food plots
• Bush Hogging
• Disking
• Site prep
Nice to have
• i have included a image of a business card that i like. I would like mine to be similar.

```html
<!DOCTYPE html>
<html lang="en">
<head>
<meta charset="utf-8">
<title>K &amp; R Acre Works – Business Card</title>
<link rel="stylesheet" href="https://fonts.googleapis.com/css2?family=Roboto+Condensed:wght@400;700&family=Roboto:wght@400&display=swap">
<style>
  :root {
    --page-bg: #2b2b2b;
    --olive: #979537;
    --olive-light: #b3b155;
    --white: #ffffff;
    --brand-brown: #a5661c;
    --tagline-dark: #2a2a22;
  }
  html, body {
    margin: 0;
    width: 1200px;
    height: 960px;
    overflow: hidden;
    background: var(--page-bg);
  }
  .business-card {
    position: absolute;
    left: 300px;
    top: 310px;
    width: 600px;
    height: 342px;
    border-radius: 14px;
    overflow: hidden;
    background: var(--olive);
  }
  .card-art {
    position: absolute;
    inset: 0;
    width: 600px;
    height: 342px;
  }
  .brand {
    position: absolute;
    left: 12px;
    top: 124px;
    display: flex;
    align-items: center;
    gap: 6px;
  }
  .brand-mark {
    width: 22px;
    height: 22px;
    background: var(--brand-brown);
  }
  .brand-name {
    font-family: "Roboto Condensed", sans-serif;
    font-weight: 700;
    font-size: 22px;
    letter-spacing: 0.3px;
    color: var(--brand-brown);
    text-transform: uppercase;
  }
  .brand-tagline {
    position: absolute;
    left: 12px;
    top: 154px;
    font-family: "Roboto Condensed", sans-serif;
    font-size: 11px;
    color: var(--tagline-dark);
    text-transform: uppercase;
    letter-spacing: 0.4px;
  }
  .contact-block {
    position: absolute;
    right: 30px;
    top: 146px;
    text-align: right;
    color: var(--white);
  }
  .person-name {
    font-family: "Roboto Condensed", sans-serif;
    font-weight: 700;
    font-size: 21px;
    line-height: 1.1;
    margin: 0;
  }
  .person-role {
    font-family: "Roboto Condensed", sans-serif;
    font-size: 15px;
    line-height: 1.1;
    margin: 2px 0 10px;
  }
  .contact-line {
    font-family: "Roboto", sans-serif;
    font-size: 14.5px;
    line-height: 18px;
    margin: 0;
  }
  .services-heading {
    font-family: "Roboto Condensed", sans-serif;
    font-weight: 700;
    font-size: 17px;
    margin: 10px 0 3px;
  }
  .service-line {
    font-family: "Roboto", sans-serif;
    font-size: 14.5px;
    line-height: 18px;
    margin: 0;
  }
</style>
</head>
<body>
  <div class="business-card">
    <svg class="card-art" viewBox="0 0 600 342" xmlns="http://www.w3.org/2000/svg">
      <defs>
        <linearGradient id="dozerPhotoTone" x1="0" y1="0" x2="0.6" y2="1">
          <stop offset="0" stop-color="#4f6a3c"/>
          <stop offset="0.35" stop-color="#c9bb3a"/>
          <stop offset="0.6" stop-color="#38404a"/>
          <stop offset="1" stop-color="#4a3a2a"/>
        </linearGradient>
        <linearGradient id="tractorPhotoTone" x1="0" y1="0" x2="0" y2="1">
          <stop offset="0" stop-color="#4c6a3a"/>
          <stop offset="0.5" stop-color="#d8552a"/>
          <stop offset="1" stop-color="#9a8a55"/>
        </linearGradient>
      </defs>
      <path d="M0 0 H356 C 330 120, 260 260, 140 342 H0 Z" fill="url(#dozerPhotoTone)"
            role="img" aria-label="Photo of a yellow bulldozer clearing dirt on a wooded site"/>
      <path d="M386 18 C 370 150, 280 280, 120 342" fill="none" stroke="var(--olive-light)" stroke-width="3"/>
      <path d="M356 0 C 340 130, 270 270, 150 342" fill="none" stroke="var(--olive)" stroke-width="8"/>
      <circle cx="508" cy="75" r="60" fill="url(#tractorPhotoTone)" stroke="#ffffff" stroke-width="2"
              role="img" aria-label="Photo of an orange tractor with front loader in a field"/>
    </svg>

    <div class="brand">
      <div class="brand-mark"></div>
      <div class="brand-name">K &amp; R Acre Works</div>
    </div>
    <div class="brand-tagline">For all your land clearing needs</div>

    <div class="contact-block">
      <p class="person-name">WADE COLTON</p>
      <p class="person-role">OWNER</p>
      <p class="contact-line">P. 601-472-3358</p>
      <p class="contact-line">wcr4817@fieldmail-example.com</p>
      <p class="contact-line">www.kracreworks-example.com</p>
      <p class="services-heading">WE CREADED</p>
      <p class="service-line">Land Clearing • Wildlife food plots •</p>
      <p class="service-line">Bush Hogging • Disking • Site prep •</p>
    </div>
  </div>
</body>
</html>
```